Luxury Wine Label for New Startup Winery

We need a wine label for our new winery startup. We have worked with a local designer but do not feel the resulting label / logo have the elevation required to present our brand as a luxury wine. Our winery is called "Quailbrook Vineyards" and we are focused on extremely high quality hand crafted artisan and estate wines from the Pacific Northwest.
We would like to see designs that utilize a tree line, or other imagery that represents the "Quailbrook" part of our company name. Another interesting feature could be wood grain.
A logo will be required based on your design so please design with this in mind:
This logo should be consistent with the wine bottle label design, and should be representative of our high end exclusive wine while giving a sense of place (Oregon/ Pacific Northwest.)
I will supply an image of the design we received from our local designer, PLEASE NOTE: in general we do like wood grain and tree line concepts but feel the execution was poorly done.
ATTN: Logo design should be suitable for use on: Bottles (Red wine/rose/white wine), Bussiness cards, vehicle signage, business signage, etc
P.S.:
If you have a design that is not outside the box we are still interested in seeing it.
Label is for a burgundy style bottle with a label height of 3.5 - 4" and a width of 3.5-4"
any label <= 4"x4" and >=3.5"x3.5" will be acceptable:
HOWEVER Width should be greater than or equal to height due to the bottle format
Target Market(s)
Wine enthusiasts with adequate discretionary budgets to afford $100 bottles of wine.
Industry/Entity Type
Wine / Winery
Requirements
Must have
- A sense of luxury, a feel of exclusivity, and a theme consistent with our product and brand name
Nice to have
- Tree line, wood grain or other wood themes. Serif fonts
Should not have
- anything cheesy, off topic, hard to read script fonts or anything that makes the label hard to read from a few feet away or too busy

```html
<!DOCTYPE html>
<html lang="en">
<head>
<meta charset="utf-8">
<title>Quailbrook Vineyard – Syrah Label</title>
<link rel="stylesheet" href="https://fonts.googleapis.com/css2?family=Montserrat:wght@700&family=Libre+Baskerville&family=Cinzel:wght@500&display=swap">
<style>
  :root {
    --backdrop: #ebebea;
    --burgundy: #7a1b2e;
    --burgundy-deep: #5e1222;
    --gold: #c9a64a;
    --gold-dark: #a9853a;
    --cream: #efe9e0;
    --ink-burgundy: #6e1527;
  }
  * { margin: 0; padding: 0; box-sizing: border-box; }
  html, body {
    width: 800px;
    height: 1200px;
    overflow: hidden;
    background: var(--backdrop);
  }
  .label {
    position: absolute;
    left: 40px;
    top: 260px;
    width: 720px;
    height: 680px;
    background: var(--burgundy);
    overflow: hidden;
  }
  .label__grain {
    position: absolute;
    inset: 0;
    background: linear-gradient(180deg, var(--burgundy) 0%, #741929 60%, var(--burgundy) 100%);
  }
  .label__top-border {
    position: absolute;
    left: 0; top: 0;
    width: 100%;
    height: 16px;
    background: linear-gradient(180deg, var(--gold) 0%, var(--gold-dark) 100%);
  }
  .brand-mark {
    position: absolute;
    left: 50%;
    top: 70px;
    width: 150px;
    height: 150px;
    margin-left: -75px;
    border-radius: 50%;
    background: var(--gold);
  }
  .brand {
    position: absolute;
    left: 60px;
    width: 600px;
    top: 262px;
    font-family: "Montserrat", sans-serif;
    font-weight: 700;
    color: var(--gold);
    line-height: 1;
  }
  .brand__name {
    display: block;
    text-align: center;
    font-size: 78px;
    letter-spacing: 0;
  }
  .brand__sub {
    display: block;
    margin-top: 8px;
    text-align: right;
    font-size: 42px;
    letter-spacing: 1px;
  }
  .origin {
    position: absolute;
    left: 0; top: 440px;
    width: 100%;
    height: 112px;
    background: var(--cream);
    text-align: center;
    font-family: "Libre Baskerville", serif;
    color: var(--ink-burgundy);
  }
  .origin__region {
    display: block;
    padding-top: 24px;
    font-size: 32px;
    letter-spacing: 1px;
  }
  .origin__vintage {
    display: block;
    margin-top: 8px;
    font-size: 24px;
    letter-spacing: 2px;
  }
  .varietal-band {
    position: absolute;
    left: 0; top: 556px;
    width: 100%;
    height: 92px;
    border-top: 5px solid var(--gold);
    border-bottom: 5px solid var(--gold);
  }
  .varietal-band__pattern {
    position: absolute;
    inset: 0;
    background: linear-gradient(90deg, #6a1626, #8b3a2e 50%, #6a1626);
  }
  .varietal {
    position: absolute;
    left: 50%;
    top: -5px;
    width: 430px;
    height: 92px;
    margin-left: -215px;
    background: var(--burgundy-deep);
    border: 5px solid var(--gold);
    display: flex;
    align-items: center;
    justify-content: center;
    font-family: "Cinzel", serif;
    font-weight: 500;
    font-size: 58px;
    letter-spacing: 2px;
    color: var(--cream);
  }
  .label__base {
    position: absolute;
    left: 0; bottom: 0;
    width: 100%;
    height: 32px;
    background: var(--burgundy-deep);
  }
</style>
</head>
<body>
  <div class="label">
    <div class="label__grain" role="img" aria-label="Burgundy wood grain texture"></div>
    <div class="label__top-border" role="img" aria-label="Gold ornamental border"></div>

    <div class="brand-mark"></div>
    <div class="brand">
      <span class="brand__name">QUAILBROOK</span>
      <span class="brand__sub">Vineyard</span>
    </div>

    <div class="origin">
      <span class="origin__region">WILLAMETTE VALLEY</span>
      <span class="origin__vintage">-2024-</span>
    </div>

    <div class="varietal-band">
      <div class="varietal-band__pattern" role="img" aria-label="Woven burgundy and gold decorative pattern"></div>
      <div class="varietal">SYRAH</div>
    </div>

    <div class="label__base"></div>
  </div>
</body>
</html>
```